Looking for a dynamic business card for a pizzeria.

A business card with our food, logo, and space for name, title, email, website, phone. The card should convey quality, unique, amazing. On the front, I envision food photo or photos with the owners names and contact information. On the back, more food with locations, website, facebook, twitter, instagram icons. It should look polished, not cartoonish, or plain.
Target Market(s)
upscale, local food buyers, 30-50 years in age.
Industry/Entity Type
Restaurant
Contact Information for Business Card
Business Name: Bru'nettix, LLC
Website: www.brunettix.com
Back:
2 locations: (can list on the back of card)
1. Harborview
4087 Corlan Avenue
Larkfield, WA 98412
360-481-5067
2. Cedar Knoll
7315 Wendmere Road
Larkfield, WA 98417
360-293-8840
front:
EDITABLE space for
Business name
Person's Name
title
2nd title
Email address
cell-phone number
Requirements
Must have
- logo
- my food photo or photos (no watermarks showing)
- locations on back
- Person contact information on front
- full bleed

```html
<!DOCTYPE html>
<html lang="en">
<head>
<meta charset="utf-8">
<title>Bru'nettix, LLC – Business Card</title>
<link href="https://fonts.googleapis.com/css2?family=Jost:wght@400;500;600;700&display=swap" rel="stylesheet">
<style>
  :root {
    --bg: #e9e4dc;
    --red: #b8141b;
    --red-deep: #9c0f15;
    --green: #1f5a2e;
    --white: #ffffff;
    --blush: #f6e4e4;
    --text-light: #ffffff;
  }
  * { box-sizing: border-box; margin: 0; padding: 0; }
  html, body { width: 1200px; height: 843px; overflow: hidden; }
  body {
    background: var(--bg);
    font-family: "Jost", sans-serif;
    position: relative;
  }
  .card {
    position: absolute;
    left: 267px;
    width: 665px;
    height: 380px;
    overflow: hidden;
    box-shadow: 0 6px 18px rgba(0,0,0,0.25);
  }
  .card--photos { top: 26px; background: var(--white); }
  .card--contact { top: 436px; background: var(--red); }

  /* Photo side */
  .photo { position: absolute; top: 0; height: 100%; }
  .photo--sandwich {
    left: 0; width: 230px;
    clip-path: polygon(0 0, 100% 0, 87% 100%, 0 100%);
    background: linear-gradient(160deg, #c99a55 0%, #8c9a3c 45%, #c8452c 100%);
  }
  .photo--salami {
    left: 190px; width: 300px;
    clip-path: polygon(10% 0, 100% 0, 90% 100%, 0 100%);
    background: radial-gradient(ellipse at 45% 50%, #e6b3a3 0%, #c97c6c 55%, #8f4a3f 100%);
  }
  .photo--kitchen {
    left: 440px; width: 225px;
    clip-path: polygon(13% 0, 100% 0, 100% 100%, 0 100%);
    background: linear-gradient(200deg, #f2ddd0 0%, #d7764a 50%, #8a3b22 100%);
  }
  .card__stripes { position: absolute; inset: 0; pointer-events: none; }
  .brand-mark {
    display: flex; align-items: center; gap: 8px;
    color: var(--green);
    font-weight: 700;
    letter-spacing: 1px;
    white-space: nowrap;
  }
  .brand-mark__dot {
    width: 22px; height: 22px; border-radius: 50%;
    background: var(--red);
    flex: none;
  }
  .card--photos .brand-mark {
    position: absolute;
    left: 222px; top: 172px;
    font-size: 24px;
  }

  /* Contact side */
  .card__shape { position: absolute; inset: 0; }
  .contact {
    position: absolute;
    left: 34px; top: 26px;
    color: var(--text-light);
    font-size: 15px;
    line-height: 1.3;
    width: 250px;
  }
  .contact__line { display: flex; align-items: center; gap: 9px; }
  .contact__line svg { width: 13px; height: 13px; flex: none; }
  .contact__divider {
    border-top: 2px dotted rgba(255,255,255,0.8);
    margin: 9px 0 8px;
    width: 200px;
  }
  .location__name, .location__phone { font-weight: 600; }
  .identity {
    position: absolute;
    left: 385px; top: 125px;
  }
  .identity .brand-mark { font-size: 34px; }
  .identity .brand-mark__dot { width: 26px; height: 26px; }
  .identity__name {
    margin: 18px 0 0 20px;
    color: var(--red);
    font-weight: 600;
    font-size: 24px;
    letter-spacing: 1px;
  }
  .identity__title {
    margin: 4px 0 0 20px;
    color: var(--green);
    font-weight: 600;
    font-size: 17px;
  }
</style>
</head>
<body>

<section class="card card--photos">
  <div class="photo photo--sandwich" role="img" aria-label="Photo of a toasted sandwich with greens and tomato"></div>
  <div class="photo photo--salami" role="img" aria-label="Close-up photo of sliced cured meats"></div>
  <div class="photo photo--kitchen" role="img" aria-label="Photo of pizza toppings being prepared in the kitchen"></div>
  <svg class="card__stripes" viewBox="0 0 665 380" aria-hidden="true">
    <polygon points="208,0 230,0 200,380 178,380" fill="var(--white)"/>
    <polygon points="213,0 219,0 189,380 183,380" fill="var(--red)"/>
    <polygon points="222,0 226,0 196,380 192,380" fill="var(--green)"/>
    <polygon points="461,0 483,0 460,380 438,380" fill="var(--white)"/>
    <polygon points="466,0 472,0 449,380 443,380" fill="var(--green)"/>
    <polygon points="475,0 479,0 456,380 452,380" fill="var(--red)"/>
  </svg>
  <div class="brand-mark">
    <span class="brand-mark__name">BRU'NETTIX</span>
    <span class="brand-mark__dot"></span>
  </div>
</section>

<section class="card card--contact">
  <svg class="card__shape" viewBox="0 0 665 380" aria-hidden="true">
    <path d="M665,45 L470,45 C360,45 300,160 330,380 L665,380 Z" fill="var(--white)"/>
    <path d="M475,58 C375,62 318,170 346,380" fill="none" stroke="var(--green)" stroke-width="4"/>
    <path d="M462,47 C358,54 305,170 333,380" fill="none" stroke="var(--red-deep)" stroke-width="3"/>
    <circle cx="560" cy="320" r="55" fill="var(--blush)"/>
    <circle cx="640" cy="100" r="40" fill="var(--blush)"/>
  </svg>

  <div class="contact">
    <p class="contact__line">
      <svg viewBox="0 0 14 14"><rect x="3" y="1" width="8" height="12" rx="1.5" fill="none" stroke="#fff" stroke-width="1.5"/></svg>
      689 512 7064
    </p>
    <p class="contact__line">
      <svg viewBox="0 0 14 14"><rect x="1" y="3" width="12" height="8" fill="#fff"/><path d="M1,3 L7,8 L13,3" fill="none" stroke="var(--red)" stroke-width="1.2"/></svg>
      name@brunettix.com
    </p>
    <p class="contact__line">
      <svg viewBox="0 0 14 14"><circle cx="7" cy="7" r="6" fill="#fff"/><path d="M1,7 H13 M7,1 C4,4 4,10 7,13 M7,1 C10,4 10,10 7,13" fill="none" stroke="var(--red)" stroke-width="1"/></svg>
      www.brunettix.com
    </p>
    <div class="contact__divider"></div>
    <div class="location">
      <p class="location__name">Harborview</p>
      <p>4087 Corlan Avenue</p>
      <p>Larkfield, WA 98412</p>
      <p class="location__phone">Phone:360-481-5067</p>
    </div>
    <div class="contact__divider"></div>
    <div class="location">
      <p class="location__name">Cedar Knoll</p>
      <p>7315 Wendmere Road</p>
      <p>Larkfield, WA 98417</p>
      <p class="location__phone">Phone:360-293-8840</p>
    </div>
  </div>

  <div class="identity">
    <div class="brand-mark">
      <span class="brand-mark__name">BRU'NETTIX</span>
      <span class="brand-mark__dot"></span>
    </div>
    <p class="identity__name">DANA MORROW</p>
    <p class="identity__title">FOUNDER</p>
  </div>
</section>

</body>
</html>
```